professional business card design for technology company

We are a small technology consulting firm, specialising in consulting based around Cloud and Managed services. Our colour scheme is yellow, blue and white, as you can see in the logos. Although we are based in melbourne australia, due to the nature of our work, our clients can be located anywhere. We are looking for a clean, professional, positive look - similar to our company logo

Target Market(s)

small business

Industry/Entity Type

Business

Contact Information for Business Card

eye catching, designed to incorporate some level of raised printing. Must contain website address, phone number, name and job title

Requirements
Must have
• Logo (attached) - use of the same colour scheme

```html
<!DOCTYPE html>
<html lang="en">
<head>
<meta charset="utf-8">
<title>Nimbora — Business Card</title>
<link rel="stylesheet" href="https://fonts.googleapis.com/css2?family=Raleway:wght@400;500;700;800&display=swap">
<style>
  :root {
    --bg: #d9d6d2;
    --card-top: #2a2a2a;
    --card-bottom: #161616;
    --white: #f4f4f4;
    --blue: #29a8e0;
    --yellow: #f2d40a;
    --grey: #8a8a8a;
    --muted: #6f6f6f;
  }
  * { margin: 0; padding: 0; box-sizing: border-box; }
  html, body { width: 1200px; height: 960px; overflow: hidden; }
  body {
    background: var(--bg);
    font-family: "Raleway", Arial, sans-serif;
    display: flex;
    flex-direction: column;
    align-items: center;
    justify-content: center;
    gap: 30px;
  }
  .card {
    width: 760px;
    height: 434px;
    background: linear-gradient(160deg, var(--card-top), var(--card-bottom));
    position: relative;
    overflow: hidden;
    box-shadow: 0 6px 18px rgba(0,0,0,0.25);
  }

  /* Front */
  .card--front {
    display: flex;
    flex-direction: column;
    align-items: center;
    justify-content: center;
    gap: 22px;
  }
  .wordmark {
    display: flex;
    align-items: center;
    gap: 18px;
  }
  .wordmark__dot {
    width: 34px; height: 34px;
    border-radius: 50%;
    background: var(--blue);
    flex: none;
  }
  .wordmark__name {
    font-weight: 800;
    font-size: 92px;
    color: var(--white);
    letter-spacing: -1px;
    line-height: 1;
    white-space: nowrap;
  }
  .front__url {
    font-size: 15px;
    letter-spacing: 12px;
    color: var(--muted);
    font-weight: 500;
    white-space: nowrap;
  }
  .accent { color: var(--blue); }

  /* Back */
  .card--back .wordmark {
    position: absolute;
    top: 38px;
    left: 150px;
    gap: 14px;
  }
  .card--back .wordmark__dot { width: 14px; height: 14px; background: var(--yellow); }
  .card--back .wordmark__name { font-size: 60px; }

  .contact {
    position: absolute;
    left: 90px;
    top: 150px;
  }
  .person {
    display: flex;
    align-items: center;
    gap: 14px;
    margin-bottom: 40px;
  }
  .icon-box {
    width: 34px; height: 34px;
    flex: none;
    border: 2px solid var(--blue);
    border-radius: 3px;
    display: flex; align-items: center; justify-content: center;
  }
  .icon-box--small {
    width: 26px; height: 26px;
    border: 1.5px solid var(--white);
  }
  .person__name {
    font-weight: 700;
    font-size: 19px;
    color: var(--white);
    letter-spacing: 0.5px;
    white-space: nowrap;
  }
  .person__name .last { color: var(--blue); font-weight: 500; }
  .person__title {
    font-size: 13px;
    color: var(--grey);
  }
  .contact__list { list-style: none; display: flex; flex-direction: column; gap: 16px; }
  .contact__item {
    display: flex; align-items: center; gap: 14px;
    font-size: 14px; color: var(--white); font-weight: 500;
  }
  .contact__text { white-space: nowrap; }

  .back__mark {
    position: absolute;
    right: 60px;
    bottom: 80px;
    font-weight: 800;
    font-size: 70px;
    color: var(--white);
    letter-spacing: -1px;
    white-space: nowrap;
  }
</style>
</head>
<body>

  <section class="card card--front" aria-label="Card front">
    <div class="wordmark">
      <span class="wordmark__dot"></span>
      <span class="wordmark__name">Nimbora</span>
    </div>
    <p class="front__url">www.nimb<span class="accent">o</span>ra.com</p>
  </section>

  <section class="card card--back" aria-label="Card back">
    <div class="wordmark">
      <span class="wordmark__dot"></span>
      <span class="wordmark__name">Nimbora</span>
    </div>

    <div class="contact">
      <div class="person">
        <span class="icon-box">
          <svg width="16" height="16" viewBox="0 0 16 16"><circle cx="8" cy="5" r="3.2" fill="#f4f4f4"/><path d="M2 15c0-3.5 2.7-5.5 6-5.5s6 2 6 5.5z" fill="#f4f4f4"/></svg>
        </span>
        <div>
          <p class="person__name">DANIEL <span class="last">HART</span></p>
          <p class="person__title">Sales Director</p>
        </div>
      </div>

      <ul class="contact__list">
        <li class="contact__item">
          <span class="icon-box icon-box--small">
            <svg width="12" height="12" viewBox="0 0 12 12"><path d="M2.5 1h2l1 3-1.3 1a6 6 0 0 0 2.8 2.8L8 6.5l3 1v2A1.5 1.5 0 0 1 9.5 11 8.5 8.5 0 0 1 1 2.5 1.5 1.5 0 0 1 2.5 1z" fill="#29a8e0"/></svg>
          </span>
          <span class="contact__text">502-555-0148</span>
        </li>
        <li class="contact__item">
          <span class="icon-box icon-box--small">
            <svg width="13" height="13" viewBox="0 0 14 14"><circle cx="7" cy="7" r="6" fill="none" stroke="#29a8e0" stroke-width="1.4"/><ellipse cx="7" cy="7" rx="2.6" ry="6" fill="none" stroke="#29a8e0" stroke-width="1.2"/><line x1="1" y1="7" x2="13" y2="7" stroke="#29a8e0" stroke-width="1.2"/></svg>
          </span>
          <span class="contact__text">www.nimb<span class="accent">o</span>ra.com</span>
        </li>
        <li class="contact__item">
          <span class="icon-box icon-box--small">
            <svg width="13" height="10" viewBox="0 0 14 10"><rect x="0.5" y="0.5" width="13" height="9" fill="#29a8e0"/><path d="M0.5 0.5 7 5.5l6.5-5" fill="none" stroke="#161616" stroke-width="1.2"/></svg>
          </span>
          <span class="contact__text">hello@nimbora.com</span>
        </li>
      </ul>
    </div>

    <p class="back__mark">Nimbora</p>
  </section>

</body>
</html>
```